Velvet Circle club

We are looking to redesign the user interface of our mobile app “Velvet Circle”, which is the official rewards program for our luxury casino brand, Kestrane Harbour.
Our goal is to give the app a more elegant, premium, and user-friendly design that reflects the exclusivity of our brand and the luxury experience we offer our VIP clientele.
What We Need:
A complete UI design for the app’s main screens, including:
Splash Screen
01 Login / Signup Screen
02 Home Dashboard
Buttons -
Home / my card / my wallet / my booking / my host
My wallet / my offer / lucky game / my taxi / entertainment / online
03 Profile screen
04 My wallet
05 My offer
06Packages
07 My booking
08 My host
09 My card
we attached our privies app all the screen for you reference
Inspiration:
Think of luxury brands like Dunmore-Vale, Corvix Onyx, or high-end lifestyle apps. Clean interfaces, classy animations, and a sense of exclusivity are key.
We’re excited to see fresh, innovative takes that elevate the app to a truly world-class luxury experience for our users.
Thank you!
Casino

```html
<!DOCTYPE html>
<html lang="en">
<head>
<meta charset="utf-8">
<title>Velvet Circle – App Screens</title>
<link href="https://fonts.googleapis.com/css2?family=Poppins:wght@400;500;600;700&family=Roboto+Condensed:wght@400;500;600&display=swap" rel="stylesheet">
<style>
  :root{
    --page:#ffffff;
    --band-light:#f2ad33;
    --band-dark:#8f5207;
    --gold:#f1a92b;
    --gold-deep:#c98612;
    --gold-text:#f6b73c;
    --login-bg:#222222;
    --app-top:#0e0c1c;
    --app-bottom:#3a2a1a;
    --white:#ffffff;
    --muted:#cfcfcf;
    --rule:#6b4a1c;
  }
  *{margin:0;padding:0;box-sizing:border-box}
  html,body{width:1200px;height:697px;overflow:hidden;background:var(--page)}
  .board{position:relative;width:1200px;height:697px;overflow:hidden;background:var(--page);font-family:"Poppins",sans-serif}
  .band{position:absolute;inset:0}
  .screen{position:absolute;top:83px;width:254px;height:531px;overflow:hidden;box-shadow:0 10px 28px rgba(0,0,0,.35);color:var(--white)}
  .screen--login{left:128px;background:radial-gradient(ellipse at 50% 100%,rgba(180,130,40,.55),rgba(34,34,34,0) 45%),var(--login-bg)}
  .screen--home{left:473px;background:linear-gradient(180deg,var(--app-top) 0%,var(--app-top) 45%,var(--app-bottom) 100%)}
  .screen--redeem{left:818px;background:linear-gradient(180deg,var(--app-top) 0%,#161223 55%,var(--app-bottom) 100%)}

  /* login */
  .brand{position:absolute;top:40px;left:0;right:0;text-align:center}
  .brand__dot{width:24px;height:24px;border-radius:50%;background:var(--gold);margin:0 auto 8px}
  .brand__name{font-weight:700;font-size:20px;letter-spacing:.5px;color:var(--gold-text);line-height:1.05}
  .brand__sub{font-weight:700;font-size:11px;color:var(--gold-text);margin-top:2px;letter-spacing:.5px}
  .login-block{position:absolute;left:0;right:0;text-align:center}
  .login-block__title{font-weight:600;font-size:15px;color:#e6e6e6;letter-spacing:.3px}
  .login-block__text{font-size:7.6px;color:var(--muted);line-height:12px;margin-top:4px;padding:0 18px}
  .pill{position:absolute;left:21px;width:211px;height:27px;border-radius:14px;background:linear-gradient(180deg,#f6b23a,#cf8d18);color:var(--white);font-family:"Roboto Condensed",sans-serif;font-weight:600;font-size:8.5px;display:flex;align-items:center;justify-content:center;letter-spacing:.2px}

  /* home */
  .topbar{position:absolute;top:20px;left:12px;right:12px;height:20px;display:flex;justify-content:space-between;align-items:center}
  .banner{position:absolute;top:74px;left:0;width:254px;height:158px;background:linear-gradient(180deg,#2a2a66 0%,#3b4fa0 45%,#1c1a3a 100%)}
  .tile{position:absolute;width:57px;height:55px;border:1.6px solid var(--gold);border-radius:3px;background:linear-gradient(180deg,#1a1520,#3a2612);display:flex;align-items:center;justify-content:center}
  .tile-label,.nav-label{position:absolute;width:80px;text-align:center;font-family:"Roboto Condensed",sans-serif;font-size:7.2px;font-weight:500;color:var(--white)}
  .nav-tile{position:absolute;top:465px;width:41px;height:38px;border:1.6px solid var(--gold);border-radius:3px;background:linear-gradient(180deg,#2a1d14,#3a2612);display:flex;align-items:center;justify-content:center}
  .nav-label{top:510px;width:60px}

  /* redeem */
  .redeem-head{position:absolute;top:22px;left:0;right:0;height:18px;text-align:center;font-family:"Roboto Condensed",sans-serif;font-size:12.5px;font-weight:500}
  .back{position:absolute;top:23px;left:17px}
  .bell-r{position:absolute;top:19px;right:12px}
  .rule{position:absolute;left:40px;width:183px;height:1px;background:var(--rule)}
  .redeem-sub{position:absolute;top:61px;left:0;right:0;text-align:center;font-size:9px}
  .step{position:absolute;left:40px;width:183px;text-align:center}
  .step__title{font-size:7px;font-weight:500}
  .step__text{font-size:6px;line-height:9.5px;margin-top:5px;color:#e8e8e8}
  svg.ic{fill:none;stroke:var(--gold);stroke-width:1.6;stroke-linecap:round;stroke-linejoin:round}
</style>
</head>
<body>
<div class="board">
  <svg class="band" width="1200" height="697" viewBox="0 0 1200 697" aria-hidden="true">
    <defs>
      <linearGradient id="bandFill" x1="0" y1="1" x2="1" y2="0">
        <stop offset="0" stop-color="var(--band-dark)"/>
        <stop offset="1" stop-color="var(--band-light)"/>
      </linearGradient>
    </defs>
    <polygon points="976,0 1200,0 1200,98 214,697 0,697 0,593" fill="url(#bandFill)"/>
  </svg>

  <!-- Login screen -->
  <section class="screen screen--login">
    <div class="brand">
      <div class="brand__dot"></div>
      <div class="brand__name">VELVET CIRCLE</div>
      <div class="brand__sub">CLUB</div>
    </div>
    <div class="login-block" style="top:146px">
      <div class="login-block__title">MEMBER LOGIN</div>
      <div class="login-block__text">Now you can enjoy al the excitement of<br>the casino right at your fingertips.</div>
    </div>
    <div class="pill" style="top:212px">SIGN IN</div>
    <div class="login-block" style="top:260px">
      <div class="login-block__title">NEW MEMBER LOGIN</div>
      <div class="login-block__text" style="padding:0 10px">If you are a first time user, please go through the signup process</div>
    </div>
    <div class="pill" style="top:326px">SIGN UP</div>
    <div class="login-block" style="top:374px">
      <div class="login-block__title">OR</div>
      <div class="login-block__text" style="margin-top:1px">If you are with a temporary d.sign in here</div>
    </div>
    <div class="pill" style="top:428px">TEMPORARY SIGN IN</div>
  </section>

  <!-- Home screen -->
  <section class="screen screen--home">
    <div class="topbar">
      <svg width="20" height="16" viewBox="0 0 20 16" aria-hidden="true"><path d="M1 2h18M1 8h18M1 14h18" stroke="#fff" stroke-width="1.6"/></svg>
      <svg width="20" height="22" viewBox="0 0 20 22" aria-hidden="true"><path d="M4 16V10a6 6 0 0 1 12 0v6l2 2H2z M8 19a2 2 0 0 0 4 0" fill="none" stroke="#fff" stroke-width="1.4"/><circle cx="16" cy="5" r="3.2" fill="#e8195a"/></svg>
    </div>
    <div class="banner" role="img" aria-label="Event banner: festive evening promotion with guests in formal wear in front of illuminated arches"></div>

    <div class="tile" style="left:16px;top:271px"><svg class="ic" width="30" height="28" viewBox="0 0 30 28"><rect x="3" y="9" width="23" height="16" rx="2"/><path d="M5 9l13-6 3 6"/><rect x="19" y="14" width="7" height="5" rx="1"/></svg></div>
    <div class="tile" style="left:98px;top:271px"><svg class="ic" width="30" height="30" viewBox="0 0 30 30"><circle cx="15" cy="15" r="11"/><path d="M10 20l10-10"/><circle cx="10.5" cy="10.5" r="1.6"/><circle cx="19.5" cy="19.5" r="1.6"/></svg></div>
    <div class="tile" style="left:180px;top:271px"><svg class="ic" width="30" height="30" viewBox="0 0 30 30"><rect x="14" y="3" width="12" height="12" rx="2"/><rect x="4" y="13" width="13" height="13" rx="2" transform="rotate(-20 10 19)"/><circle cx="10" cy="20" r="1.2"/><circle cx="18" cy="7" r="1"/><circle cx="22" cy="11" r="1"/></svg></div>
    <div class="tile-label" style="left:4px;top:336px">MY WALLET</div>
    <div class="tile-label" style="left:87px;top:336px">MY OFFER</div>
    <div class="tile-label" style="left:168px;top:336px">LUCKY GAME</div>

    <div class="tile" style="left:16px;top:360px"><svg class="ic" width="30" height="30" viewBox="0 0 30 30"><rect x="4" y="4" width="12" height="22" rx="2"/><path d="M7 15l2 2 4-4"/><path d="M23 6a4 4 0 0 1 4 4c0 3-4 7-4 7s-4-4-4-7a4 4 0 0 1 4-4z"/><path d="M18 24h9"/></svg></div>
    <div class="tile" style="left:98px;top:360px"><svg class="ic" width="30" height="30" viewBox="0 0 30 30"><path d="M4 27L12 12l7 7z"/><path d="M16 10l3-5M21 13l5-3M19 5l1 1M25 6l1 1M6 6l1 2 2 0-1 2 1 2-2-1-2 1 0-2-1-2h2z"/></svg></div>
    <div class="tile" style="left:180px;top:360px"><svg class="ic" width="30" height="30" viewBox="0 0 30 30"><rect x="4" y="3" width="14" height="24" rx="2"/><circle cx="11" cy="15" r="4"/><path d="M9 15l1.5 1.5L13 14"/><rect x="18" y="12" width="9" height="9" rx="1"/><path d="M20 15h5M20 18h5"/></svg></div>
    <div class="tile-label" style="left:4px;top:425px">MY TAXI</div>
    <div class="tile-label" style="left:87px;top:425px">ENTERTAINMENT</div>
    <div class="tile-label" style="left:168px;top:425px">ONLINE</div>

    <div class="nav-tile" style="left:9px"><svg class="ic" width="22" height="22" viewBox="0 0 22 22"><path d="M3 10L11 3l8 7v9H3z"/><path d="M9 19v-5h4v5"/></svg></div>
    <div class="nav-tile" style="left:58px"><svg class="ic" width="22" height="22" viewBox="0 0 22 22"><rect x="2" y="7" width="16" height="11" rx="1.5"/><path d="M5 4h15v11M2 11h16"/></svg></div>
    <div class="nav-tile" style="left:107px"><svg class="ic" width="22" height="22" viewBox="0 0 22 22"><rect x="2" y="7" width="17" height="12" rx="1.5"/><path d="M4 7l9-4 2 4"/><rect x="14" y="11" width="5" height="4"/></svg></div>
    <div class="nav-tile" style="left:156px"><svg class="ic" width="22" height="22" viewBox="0 0 22 22"><rect x="2" y="4" width="18" height="15" rx="1.5"/><path d="M2 8h18M6 2v4M11 2v4M16 2v4M5 12h2M10 12h2M15 12h2M5 16h2M10 16h2"/></svg></div>
    <div class="nav-tile" style="left:205px"><svg class="ic" width="22" height="22" viewBox="0 0 22 22"><rect x="5" y="2" width="14" height="18" rx="1.5"/><circle cx="12" cy="9" r="2.5"/><path d="M8 16a4 4 0 0 1 8 0M3 6h4M3 11h4M3 16h4"/></svg></div>
    <div class="nav-label" style="left:0">HOME</div>
    <div class="nav-label" style="left:48px">MY CARD</div>
    <div class="nav-label" style="left:97px">MY WALLET</div>
    <div class="nav-label" style="left:146px">MY BOOKING</div>
    <div class="nav-label" style="left:195px">MY HOGT</div>
  </section>

  <!-- Redeem screen -->
  <section class="screen screen--redeem">
    <svg class="back" width="10" height="14" viewBox="0 0 10 14" aria-hidden="true"><path d="M8 1L2 7l6 6" fill="none" stroke="var(--gold)" stroke-width="2"/></svg>
    <div class="redeem-head">HOW TO REDEEM</div>
    <svg class="bell-r" width="20" height="22" viewBox="0 0 20 22" aria-hidden="true"><path d="M4 16V10a6 6 0 0 1 12 0v6l2 2H2z M8 19a2 2 0 0 0 4 0" fill="none" stroke="#fff" stroke-width="1.4"/><circle cx="16" cy="5" r="3.2" fill="#e8195a"/></svg>
    <div class="rule" style="top:49px"></div>
    <div class="redeem-sub">How to redeem your vouchers</div>
    <div class="rule" style="top:87px"></div>

    <div class="step" style="top:99px"><div class="step__title">STEP 01</div><div class="step__text">Select the preferred Partner you want to redeem your voucher at</div></div>
    <div class="rule" style="top:142px"></div>
    <div class="step" style="top:154px"><div class="step__title">STEP 02</div><div class="step__text">Present your kestrane voucher at time of payment by showing the voucher and number appearing on your mobile</div></div>
    <div class="rule" style="top:209px"></div>
    <div class="step" style="top:221px"><div class="step__title">STEP 03</div><div class="step__text">Indicate the number and value of the voucher you want to pay with</div></div>
    <div class="rule" style="top:268px"></div>
    <div class="step" style="top:280px"><div class="step__title">STEP 04</div><div class="step__text">You will receive a message to your app indicating a successful transaction</div></div>
    <div class="rule" style="top:328px"></div>
    <div class="step" style="top:340px"><div class="step__title">STEP 05</div><div class="step__text">The transaction voucher will get deleted from your Voucher</div></div>
    <div class="rule" style="top:388px"></div>

    <div class="nav-tile" style="left:9px"><svg class="ic" width="22" height="22" viewBox="0 0 22 22"><path d="M3 10L11 3l8 7v9H3z"/><path d="M9 19v-5h4v5"/></svg></div>
    <div class="nav-tile" style="left:58px"><svg class="ic" width="22" height="22" viewBox="0 0 22 22"><rect x="2" y="7" width="16" height="11" rx="1.5"/><path d="M5 4h15v11M2 11h16"/></svg></div>
    <div class="nav-tile" style="left:107px"><svg class="ic" width="22" height="22" viewBox="0 0 22 22"><rect x="2" y="7" width="17" height="12" rx="1.5"/><path d="M4 7l9-4 2 4"/><rect x="14" y="11" width="5" height="4"/></svg></div>
    <div class="nav-tile" style="left:156px"><svg class="ic" width="22" height="22" viewBox="0 0 22 22"><rect x="2" y="4" width="18" height="15" rx="1.5"/><path d="M2 8h18M6 2v4M11 2v4M16 2v4M5 12h2M10 12h2M15 12h2M5 16h2M10 16h2"/></svg></div>
    <div class="nav-tile" style="left:205px"><svg class="ic" width="22" height="22" viewBox="0 0 22 22"><rect x="5" y="2" width="14" height="18" rx="1.5"/><circle cx="12" cy="9" r="2.5"/><path d="M8 16a4 4 0 0 1 8 0M3 6h4M3 11h4M3 16h4"/></svg></div>
    <div class="nav-label" style="left:0">HOME</div>
    <div class="nav-label" style="left:48px">MY CARD</div>
    <div class="nav-label" style="left:97px">MY WALLET</div>
    <div class="nav-label" style="left:146px">MY BOOKING</div>
    <div class="nav-label" style="left:195px">MY HOGT</div>
  </section>
</div>
</body>
</html>
```